Tolvar Air and Electrical Website

Simple and easy to use website for a Electrical and Air Conditioning contracting business.Use stock photosOnline contact portallogo still to be supplied

Target Market(s)

Mums and Dads who want a local contractor

Coding

Coded - Design and coding required

Number of Pages Required

2 page

Font styles to use
Sans Serif

Colors
f04a50
3276b5
33a6d7

Requirements
Must have
• Simple and easy to use
• Ph number
• 4 web address; linked to page
• 0417385926
• tolvar.com.au
• tolvarelectrical.com.au
• tolvarairandelectrical.com.au
• tolvarair.com.au
Nice to have
• Split System Air Con Picture
• Electrical Pictures

```html
<!DOCTYPE html>
<html lang="en">
<head>
<meta charset="utf-8">
<title>Tolvar Air and Electrical</title>
<link href="https://fonts.googleapis.com/css2?family=League+Spartan:wght@600;700&family=Open+Sans:ital,wght@0,400;0,600;0,700;1,400&family=Ubuntu:wght@400;500&display=swap" rel="stylesheet">
<style>
:root{
  --red:#f04a50;
  --red-deep:#d8283a;
  --blue:#3276b5;
  --blue-light:#33a6d7;
  --navy:#0d2a5a;
  --ink:#1d1d1f;
  --text:#555a5f;
  --grey-bg:#eceff0;
  --dark:#18191b;
  --white:#ffffff;
  --star:#d9b01c;
}
*{box-sizing:border-box;margin:0;padding:0}
html,body{width:1200px;height:3857px;overflow:hidden}
body{position:relative;background:var(--white);font-family:"Open Sans",sans-serif;color:var(--text)}
.abs{position:absolute}
.heading{font-family:"League Spartan",sans-serif;font-weight:700;color:var(--ink);letter-spacing:.5px;text-transform:uppercase}

/* header */
.site-header{position:absolute;left:0;top:0;width:1200px;height:108px;background:var(--white)}
.brand{position:absolute;left:110px;top:34px;font-family:"League Spartan",sans-serif;font-weight:700;font-size:40px;color:var(--ink);letter-spacing:1px}
.call{position:absolute;right:110px;top:16px;font-family:"Ubuntu",sans-serif;font-size:19px;color:var(--ink);display:flex;align-items:center;gap:8px}
.call strong{color:var(--blue);font-size:22px;font-weight:500}
.main-nav{position:absolute;right:108px;top:66px;display:flex;gap:27px;font-family:"Ubuntu",sans-serif;font-size:16px;color:var(--ink);align-items:center}
.main-nav .active{color:var(--red)}

/* hero */
.hero{position:absolute;left:0;top:108px;width:1200px;height:660px;background:radial-gradient(ellipse at 60% 40%,#2a6fb0 0%,#123a78 45%,#0a1f4a 100%)}
.hero-title{position:absolute;left:0;top:157px;width:1200px;text-align:center;font-size:55px;line-height:75px;color:var(--white)}
.btn-solid{position:absolute;background:var(--red);color:var(--white);font-family:"Open Sans",sans-serif;font-weight:700;font-size:17px;border-radius:33px;display:flex;align-items:center;justify-content:center;text-transform:uppercase}
.dots{position:absolute;top:610px;left:566px;display:flex;gap:6px}
.dots span{width:13px;height:13px;border-radius:50%;border:2px solid var(--white)}
.dots span:first-child{background:var(--white)}

/* welcome */
.welcome-title{left:111px;top:830px;font-size:46px;line-height:60px}
.welcome-text{left:111px;top:964px;width:410px;font-size:15px;line-height:28.5px}
.btn-outline{position:absolute;border:2px solid var(--red);color:var(--red);font-weight:700;font-size:16px;border-radius:26px;display:flex;align-items:center;justify-content:center;text-transform:uppercase}
.video{position:absolute;left:601px;top:850px;width:487px;height:328px;background:linear-gradient(135deg,#8c9aa6,#c9cfd3 55%,#6d7780);box-shadow:0 8px 20px rgba(0,0,0,.25)}
.play{position:absolute;left:213px;top:133px;width:60px;height:60px;border-radius:50%;background:rgba(0,0,0,.8)}
.play:after{content:"";position:absolute;left:23px;top:17px;border-left:20px solid var(--white);border-top:13px solid transparent;border-bottom:13px solid transparent}

/* services */
.section-title{position:absolute;left:0;width:1200px;text-align:center;font-size:46px}
.service-card{position:absolute;top:1493px;width:310px;height:320px;background:var(--white);text-align:center;border-bottom:5px solid var(--blue)}
.service-card.accent{border-bottom-color:var(--red)}
.service-icon{width:105px;height:105px;border-radius:50%;background:var(--blue);margin:26px auto 0;display:flex;align-items:center;justify-content:center}
.accent .service-icon{background:var(--red)}
.service-name{font-family:"Ubuntu",sans-serif;font-size:24px;color:var(--ink);margin-top:22px}
.service-text{font-size:15px;line-height:26.5px;margin:14px auto 0;width:250px}
.slider-arrow{position:absolute;top:1633px}

/* testimonials */
.stars{position:absolute;left:548px;top:2116px;display:flex;gap:2px}
.quote{position:absolute;left:200px;top:2158px;width:800px;text-align:center;font-style:italic;font-size:16px;line-height:31px}
.avatar{position:absolute;border-radius:50%;background:linear-gradient(160deg,#d7dadc,#9aa1a6)}
.avatar.main{background:linear-gradient(160deg,#6f6a66,#3b3735)}
.client-name{position:absolute;left:0;top:2380px;width:1200px;text-align:center;color:var(--red);font-weight:700;font-size:16px}
.client-role{position:absolute;left:0;top:2407px;width:1200px;text-align:center;color:var(--ink);font-size:14px}

/* why */
.why-photo{position:absolute;left:52px;top:2532px;width:518px;height:598px;background:linear-gradient(180deg,#f0c63a 0%,#c9a07f 14%,#2b3b6b 30%,#1e2c55 100%);border-radius:40% 40% 6px 6px / 18% 18% 6px 6px}
.why-title{position:absolute;left:612px;top:2650px;font-size:46px;color:var(--white)}
.why-text{position:absolute;left:612px;top:2718px;width:500px;font-size:15px;line-height:29px;color:var(--white)}
.why-list{position:absolute;left:612px;top:2806px;width:520px;display:grid;grid-template-columns:240px 280px;row-gap:13px;list-style:none;color:var(--white);font-size:15px}
.why-list li{display:flex;align-items:center;gap:8px;height:24px}

/* contact */
.contact-title{color:var(--white)}
.sub-title{position:absolute;font-family:"Ubuntu",sans-serif;font-size:23px;color:var(--white)}
.field{position:absolute;border:2px solid #d9d9d9;border-radius:6px;color:var(--white);font-size:14px;padding:12px 14px}
.info-row{position:absolute;left:778px;display:flex;align-items:center;gap:16px;color:var(--white);font-size:14px;line-height:24px}
.info-icon{width:36px;height:36px;border-radius:50%;border:1.5px solid var(--white);display:flex;align-items:center;justify-content:center;flex:none}
.social{position:absolute;top:3688px;width:35px;height:35px;border-radius:50%;border:1.5px solid var(--white)}
.footer-line{position:absolute;left:111px;top:3763px;width:969px;height:1px;background:#4a4b4e}
.copyright{position:absolute;left:0;top:3804px;width:1200px;text-align:center;color:var(--white);font-size:14px}
</style>
</head>
<body>

<header class="site-header">
  <div class="brand">TOLVAR</div>
  <div class="call">
    <svg width="16" height="16" viewBox="0 0 24 24"><path fill="#f04a50" d="M6.6 10.8a15 15 0 0 0 6.6 6.6l2.2-2.2c.3-.3.7-.4 1-.2 1.1.4 2.3.6 3.6.6.6 0 1 .4 1 1V20c0 .6-.4 1-1 1A17 17 0 0 1 3 4c0-.6.4-1 1-1h3.5c.6 0 1 .4 1 1 0 1.3.2 2.5.6 3.6.1.3 0 .7-.2 1z"/></svg>
    Call us on: <strong>0417385926</strong>
  </div>
  <nav class="main-nav">
    <span class="active">HOME</span><span>ABOUT US</span><span>SERVICES</span><span>CAREERS</span><span>BLOG</span><span>CONTACT</span>
    <svg width="15" height="15" viewBox="0 0 24 24"><circle cx="10" cy="10" r="7" fill="none" stroke="#1d1d1f" stroke-width="3"/><path d="M15 15l6 6" stroke="#1d1d1f" stroke-width="3.5" stroke-linecap="round"/></svg>
  </nav>
</header>

<section class="hero" role="img" aria-label="Close-up photograph of glowing blue and red circuit board traces">
  <h1 class="heading hero-title">Electrical &amp; Air Conditioning<br>Contracting Business</h1>
  <div class="btn-solid" style="left:497px;top:337px;width:206px;height:66px">Get a Free Quote</div>
  <div class="dots"><span></span><span></span><span></span><span></span></div>
</section>
<svg class="abs" style="left:0;top:660px" width="1200" height="120" viewBox="0 0 1200 120">
  <polygon points="0,8 1200,62 1200,120 0,120" fill="#3276b5"/>
  <polygon points="0,38 1200,80 1200,120 0,120" fill="#33a6d7"/>
  <polygon points="0,68 1200,108 1200,120 0,120" fill="#ffffff"/>
</svg>

<h2 class="abs heading welcome-title">Welcome to<br>Tolvar</h2>
<p class="abs welcome-text">Nam libero tempore, cum soluta nobis est eligendi opticum que nihil impedit quo minus id quod maxime placeat facere possimus, omnis voluptas assumenda est, omnis dolorpelle ndus. Temporibus autem quibusdam et aut officiis debitaut rerum necessitatibus saepe eiciend.</p>
<div class="btn-outline" style="left:111px;top:1138px;width:157px;height:50px">Read More</div>
<div class="video" role="img" aria-label="Video still of a technician servicing rooftop air conditioning units"><span class="play"></span></div>

<svg class="abs" style="left:0;top:1262px" width="1200" height="690" viewBox="0 0 1200 690">
  <polygon points="0,67 1200,0 1200,643 0,688" fill="#eceff0"/>
</svg>
<h2 class="heading section-title" style="top:1382px">What We Do</h2>

<svg class="slider-arrow" style="left:42px" width="20" height="34" viewBox="0 0 20 34"><path d="M17 3L4 17l13 14" fill="none" stroke="#555" stroke-width="3.5"/></svg>
<svg class="slider-arrow" style="left:1138px" width="20" height="34" viewBox="0 0 20 34"><path d="M3 3l13 14L3 31" fill="none" stroke="#555" stroke-width="3.5"/></svg>

<article class="service-card" style="left:111px">
  <div class="service-icon"><svg width="48" height="48" viewBox="0 0 24 24"><path fill="#fff" d="M21 6.5a5 5 0 0 1-6.7 4.7L6 19.5a2 2 0 0 1-2.8-2.8l8.3-8.3A5 5 0 0 1 17.5 2l-3 3 .5 3 3 .5z"/></svg></div>
  <h3 class="service-name">Electrical Repair</h3>
  <p class="service-text">Nam libero tempore, cum soluta nobis est eligendi optio cumque ni hil impedit quo minus id</p>
</article>
<article class="service-card accent" style="left:445px">
  <div class="service-icon"><svg width="50" height="50" viewBox="0 0 24 24"><path fill="#fff" d="M3 8h14l-3-3 1.4-1.4L21 9l-5.6 5.4L14 13l3-3H3zm18 6H7l3 3-1.4 1.4L3 13l5.6-5.4L10 9 7 12h14z" transform="translate(0 1)"/></svg></div>
  <h3 class="service-name">Electrical Replacement</h3>
  <p class="service-text">Nam libero tempore, cum soluta nobis est eligendi optio cumque ni hil impedit quo minus id</p>
</article>
<article class="service-card" style="left:779px">
  <div class="service-icon"><svg width="54" height="54" viewBox="0 0 24 24"><g fill="#fff"><circle cx="9" cy="13" r="5"/><circle cx="17" cy="7" r="3"/><circle cx="18" cy="17" r="2.5"/></g><g fill="#3276b5"><circle cx="9" cy="13" r="2"/><circle cx="17" cy="7" r="1.2"/><circle cx="18" cy="17" r="1"/></g></svg></div>
  <h3 class="service-name">Electrical Maintenance</h3>
  <p class="service-text">Nam libero tempore, cum soluta nobis est eligendi optio cumque ni hil impedit quo minus id</p>
</article>

<h2 class="heading section-title" style="top:2033px">Client Testimonials</h2>
<div class="stars">
  <svg width="104" height="22" viewBox="0 0 104 22">
    <g fill="#d9b01c" stroke="#d9b01c" stroke-width="1.2">
      <path id="st" d="M10 1l2.8 6 6.4.7-4.8 4.3 1.4 6.4L10 15l-5.8 3.4 1.4-6.4L.8 7.7 7.2 7z"/>
      <use href="#st" x="21"/><use href="#st" x="42"/><use href="#st" x="63"/>
    </g>
    <use href="#st" x="84" fill="none" stroke="#d9b01c" stroke-width="1.5"/>
  </svg>
</div>
<p class="quote">Nemo enim ipsam voluptatem quia voluptas sit aspernatur aut odit aut fugit, sed quia consequuntur magni dolores eos qui ratione voluptatem eque porro quisquam est, qui dolorem ipsum quia dt</p>
<div class="avatar" style="left:447px;top:2258px;width:84px;height:84px" role="img" aria-label="Client portrait"></div>
<div class="avatar main" style="left:550px;top:2250px;width:100px;height:100px" role="img" aria-label="Featured client portrait"></div>
<div class="avatar" style="left:669px;top:2258px;width:84px;height:84px" role="img" aria-label="Client portrait"></div>
<div class="client-name">LIAM CARTER</div>
<div class="client-role">Eiusmod tempor incid</div>

<svg class="abs" style="left:0;top:2500px" width="1200" height="740" viewBox="0 0 1200 740">
  <defs><linearGradient id="redfade" x1="0" y1="0" x2="1" y2="1"><stop offset="0" stop-color="#e03340"/><stop offset="1" stop-color="#f04a50"/></linearGradient></defs>
  <polygon points="0,2 1200,74 1200,740 0,740" fill="url(#redfade)"/>
  <polygon points="0,618 1200,700 1200,740 0,740" fill="#3276b5"/>
  <polygon points="0,628 1200,725 1200,740 0,740" fill="#33a6d7"/>
  <polygon points="0,622 1200,740 0,740" fill="#18191b"/>
</svg>
<div class="abs" style="left:0;top:3240px;width:1200px;height:617px;background:var(--dark)"></div>

<div class="why-photo" role="img" aria-label="Photograph of a smiling electrician in a yellow hard hat and navy work overalls"></div>
<h2 class="heading why-title">Why Choose Tolvar</h2>
<p class="why-text">Nam libero tempore, cum soluta nobis est eligendi opticum que nihil impedit quo minus id quod matates repu.</p>
<ul class="why-list">
  <li><svg width="14" height="14" viewBox="0 0 16 16"><circle cx="8" cy="8" r="8" fill="#fff"/><path d="M4.5 8.2l2.3 2.3 4.7-4.8" fill="none" stroke="#e03340" stroke-width="2"/></svg>Friendly, Expert Electricians</li>
  <li><svg width="14" height="14" viewBox="0 0 16 16"><circle cx="8" cy="8" r="8" fill="#fff"/><path d="M4.5 8.2l2.3 2.3 4.7-4.8" fill="none" stroke="#e03340" stroke-width="2"/></svg>100% Satisfaction Guarantee</li>
  <li><svg width="14" height="14" viewBox="0 0 16 16"><circle cx="8" cy="8" r="8" fill="#fff"/><path d="M4.5 8.2l2.3 2.3 4.7-4.8" fill="none" stroke="#e03340" stroke-width="2"/></svg>Upfront, Honest Pricing</li>
  <li><svg width="14" height="14" viewBox="0 0 16 16"><circle cx="8" cy="8" r="8" fill="#fff"/><path d="M4.5 8.2l2.3 2.3 4.7-4.8" fill="none" stroke="#e03340" stroke-width="2"/></svg>Safe For Your Family &amp; Home</li>
  <li><svg width="14" height="14" viewBox="0 0 16 16"><circle cx="8" cy="8" r="8" fill="#fff"/><path d="M4.5 8.2l2.3 2.3 4.7-4.8" fill="none" stroke="#e03340" stroke-width="2"/></svg>Certified Electrician Team</li>
  <li><svg width="14" height="14" viewBox="0 0 16 16"><circle cx="8" cy="8" r="8" fill="#fff"/><path d="M4.5 8.2l2.3 2.3 4.7-4.8" fill="none" stroke="#e03340" stroke-width="2"/></svg>We Address All Electrical Problems</li>
  <li><svg width="14" height="14" viewBox="0 0 16 16"><circle cx="8" cy="8" r="8" fill="#fff"/><path d="M4.5 8.2l2.3 2.3 4.7-4.8" fill="none" stroke="#e03340" stroke-width="2"/></svg>We focus on the customer</li>
  <li><svg width="14" height="14" viewBox="0 0 16 16"><circle cx="8" cy="8" r="8" fill="#fff"/><path d="M4.5 8.2l2.3 2.3 4.7-4.8" fill="none" stroke="#e03340" stroke-width="2"/></svg>We operate with excellence</li>
</ul>
<div class="btn-outline" style="left:612px;top:2982px;width:157px;height:50px;border-color:#fff;color:#fff">Read More</div>

<h2 class="heading section-title contact-title" style="top:3278px">Contact Us</h2>
<div class="sub-title" style="left:110px;top:3382px">Get a Quote</div>
<div class="field" style="left:111px;top:3443px;width:297px;height:46px">Name :</div>
<div class="field" style="left:418px;top:3443px;width:296px;height:46px">Phone no :</div>
<div class="field" style="left:111px;top:3504px;width:603px;height:46px">Email :</div>
<div class="field" style="left:111px;top:3566px;width:603px;height:82px">Message :</div>
<div class="btn-solid" style="left:608px;top:3669px;width:106px;height:42px;font-size:14px;border-radius:21px">Submit</div>

<div class="sub-title" style="left:778px;top:3382px">Contact Information</div>
<div class="info-row" style="top:3436px">
  <span class="info-icon"><svg width="14" height="16" viewBox="0 0 24 24"><path fill="#fff" d="M12 2a7 7 0 0 0-7 7c0 5 7 13 7 13s7-8 7-13a7 7 0 0 0-7-7zm0 9.5A2.5 2.5 0 1 1 12 6.5a2.5 2.5 0 0 1 0 5z"/></svg></span>
  <span>14 Ridgeway Street<br>4101 Westvale</span>
</div>
<div class="info-row" style="top:3502px">
  <span class="info-icon"><svg width="14" height="14" viewBox="0 0 24 24"><path fill="#fff" d="M6.6 10.8a15 15 0 0 0 6.6 6.6l2.2-2.2c.3-.3.7-.4 1-.2 1.1.4 2.3.6 3.6.6.6 0 1 .4 1 1V20c0 .6-.4 1-1 1A17 17 0 0 1 3 4c0-.6.4-1 1-1h3.5c.6 0 1 .4 1 1 0 1.3.2 2.5.6 3.6.1.3 0 .7-.2 1z"/></svg></span>
  <span>0417385926</span>
</div>
<div class="info-row" style="top:3562px">
  <span class="info-icon"><svg width="14" height="12" viewBox="0 0 24 20"><rect x="1" y="2" width="22" height="16" rx="2" fill="#fff"/><path d="M2 4l10 7 10-7" fill="none" stroke="#18191b" stroke-width="2"/></svg></span>
  <span>info@tolvar.com.au</span>
</div>
<div class="sub-title" style="left:778px;top:3641px">Social Media</div>
<span class="social" style="left:776px" aria-label="Social profile"></span>
<span class="social" style="left:822px" aria-label="Social profile"></span>
<span class="social" style="left:868px" aria-label="Social profile"></span>

<div class="footer-line"></div>
<p class="copyright">Copyright © 2019, Tolvar. All rights reserved.</p>

</body>
</html>
```